Vantro cards

I am in the auto motive, transportation business I would like a business card that is Something cool, modern edgy, having to do with car culture. I offer towing service for high and exotic cars. I also provide towing for collisions and car accidents. I offer open and enclosed transport nationwide.

Target Market(s)

Car culture people high end auto collectors

Industry/Entity Type

Towing car carrier

Contact Information for Business Card

My company colors black yellow and silver

Font styles to use
Serif

```html
<!DOCTYPE html>
<html lang="en">
<head>
<meta charset="utf-8">
<title>Vantro business cards</title>
<link rel="stylesheet" href="https://fonts.googleapis.com/css2?family=Roboto+Slab:wght@500;700;800&display=swap">
<style>
  :root {
    --backdrop: #404040;
    --card-white: #ffffff;
    --card-black: #000000;
    --brand-yellow: #fbe060;
    --ink: #111111;
    --shadow: rgba(0,0,0,0.85);
  }
  html, body {
    margin: 0;
    padding: 0;
    width: 1075px;
    height: 1200px;
    overflow: hidden;
    background: var(--backdrop);
    font-family: "Roboto Slab", serif;
  }
  .canvas { position: relative; width: 1075px; height: 1200px; }
  .card {
    position: absolute;
    width: 663px;
    height: 395px;
    box-shadow: 3px 3px 2px var(--shadow);
    overflow: hidden;
  }
  .card--front { left: 206px; top: 187px; background: var(--card-white); }
  .card--back { left: 203px; top: 637px; background: var(--card-black); }

  .band { position: absolute; left: 0; top: 0; }

  .brand {
    position: absolute;
    display: flex;
    align-items: center;
    gap: 10px;
    transform: translate(-50%, -50%);
    font-weight: 800;
    font-size: 40px;
    letter-spacing: 1px;
    line-height: 1;
    white-space: nowrap;
  }
  .brand__mark { width: 14px; height: 14px; }
  .card--front .brand { left: 165px; top: 200px; color: var(--ink); }
  .card--front .brand__mark { background: var(--ink); }
  .card--back .brand { left: 333px; top: 199px; color: var(--brand-yellow); font-size: 48px; }
  .card--back .brand__mark { background: var(--brand-yellow); width: 16px; height: 16px; }

  .details { position: absolute; left: 0; top: 0; color: var(--ink); }
  .line { position: absolute; white-space: nowrap; line-height: 1; }
  .person__name { left: 314px; top: 87px; font-size: 23px; font-weight: 700; letter-spacing: 0.3px; }
  .person__role { left: 314px; top: 113px; font-size: 17px; font-weight: 700; }
  .address { font-size: 17px; font-weight: 700; left: 315px; }
  .contact { font-size: 17px; font-weight: 700; left: 336px; }
  .icon { position: absolute; left: 314px; width: 16px; height: 16px; }
</style>
</head>
<body>
<div class="canvas">

  <section class="card card--front">
    <svg class="band" width="663" height="395" viewBox="0 0 663 395" aria-hidden="true">
      <polygon fill="var(--brand-yellow)" points="91,0 240,0 240,97 165.5,71 91,97"/>
      <polygon fill="var(--brand-yellow)" points="91,298 165.5,324 240,298 240,395 91,395"/>
    </svg>

    <div class="brand"><span class="brand__mark"></span>VANTRO</div>

    <div class="details">
      <div class="line person__name">MARCUS HALE</div>
      <div class="line person__role">Managing Director</div>

      <div class="line address" style="top:165px">421, Address line</div>
      <div class="line address" style="top:189px">goes here 45452</div>
      <div class="line address" style="top:212px">Country Name</div>

      <svg class="icon" style="top:263px" viewBox="0 0 16 16" aria-hidden="true">
        <path fill="var(--ink)" d="M3.2 1.5l2.3 2.6-1.4 1.6c.8 1.9 2.3 3.4 4.2 4.2l1.6-1.4 2.6 2.3-1.4 2.3C6.3 13 3 9.7 1 4.9z"/>
        <path fill="none" stroke="var(--ink)" stroke-width="1.3" d="M9.5 2.5a4 4 0 0 1 4 4M9.5 0.6a6 6 0 0 1 5.9 5.9"/>
      </svg>
      <div class="line contact" style="top:263px">046-318 270 554</div>

      <svg class="icon" style="top:288px" viewBox="0 0 16 16" aria-hidden="true">
        <rect x="0.5" y="3" width="15" height="10.5" fill="var(--ink)"/>
        <path fill="none" stroke="var(--card-white)" stroke-width="1.2" d="M1 3.5l7 5.5 7-5.5M1 13l5-4.5M15 13l-5-4.5"/>
      </svg>
      <div class="line contact" style="top:288px">hello@vantromail.com</div>

      <svg class="icon" style="top:312px" viewBox="0 0 16 16" aria-hidden="true">
        <g fill="none" stroke="var(--ink)" stroke-width="1.2">
          <circle cx="8" cy="8" r="7"/>
          <ellipse cx="8" cy="8" rx="3" ry="7"/>
          <path d="M1 8h14M2 4.5h12M2 11.5h12"/>
        </g>
      </svg>
      <div class="line contact" style="top:312px">www.vantrohaul.com</div>
    </div>
  </section>

  <section class="card card--back">
    <div class="brand"><span class="brand__mark"></span>VANTRO</div>
  </section>

</div>
</body>
</html>
```